Property management company looking for modern card design

We at Blue Heron Partners provides property management services for its residential and commercial properties, with expertise in all categories of multifamily, industrial and office projects throughout California.

We need a business card design that is professional and modern designed business card. In our field, clients get hundreds of business cards, we would like our card to stand out.

Please avoid small print.

Target Market(s)

Professionals and high end clients

Industry/Entity Type

Financial Planning

Contact Information for Business Card

Company Name: Blue Heron Partners, Name, email, license #, phone number, website blueheronpartners.com

Font styles to use
Sans Serif

Requirements
Must have
• The card design needs to be adaptable because there is a possibly we will be expanding into different sectors other than real estate. The card design should be focused on financial planning and asset management.
Nice to have
• Modern and simple business card. Eye catching. Non-standard size/shaped cards would be great.
• blueheronpartners.com
Should not have
• Too many bright color or any pictures or shapes of real estate stuff.

```html
<!DOCTYPE html>
<html lang="en">
<head>
<meta charset="utf-8">
<title>Blue Heron Partners — Business Card</title>
<link rel="stylesheet" href="https://fonts.googleapis.com/css2?family=Michroma&family=Tinos&family=Open+Sans:wght@400&display=swap">
<style>
  :root {
    --backdrop: #d8d3cb;
    --paper: #e4e1da;
    --paper-edge: #cfcbc3;
    --ink: #2b2826;
    --ink-soft: #4a4643;
    --accent: #d40f0f;
    --card-dark: #2a2725;
    --on-dark: #e9e7e4;
  }
  * { box-sizing: border-box; margin: 0; padding: 0; }
  html, body { width: 1200px; height: 848px; overflow: hidden; }
  body {
    background: var(--backdrop);
    display: flex;
    align-items: center;
    justify-content: center;
    gap: 60px;
  }
  .card {
    position: relative;
    width: 520px;
    height: 297px;
    border-radius: 22px;
    box-shadow: 0 10px 28px rgba(0,0,0,0.22);
    overflow: hidden;
  }
  .card--front { background: var(--paper); border: 1px solid var(--paper-edge); }
  .card--back { background: var(--card-dark); }

  .brand { position: absolute; display: flex; flex-direction: column; align-items: center; }
  .brand__mark { background: var(--accent); }
  .brand__name {
    font-family: "Michroma", sans-serif;
    letter-spacing: 0.08em;
    text-transform: uppercase;
    white-space: nowrap;
  }
  .card--front .brand { top: 34px; right: 40px; }
  .card--front .brand__mark { width: 62px; height: 40px; margin-bottom: 12px; }
  .card--front .brand__name { font-size: 13px; color: var(--ink); }

  .card--back .brand { left: 0; right: 0; top: 78px; }
  .card--back .brand__mark { width: 104px; height: 80px; margin-bottom: 22px; }
  .card--back .brand__name { font-size: 22px; color: var(--on-dark); }

  .person {
    position: absolute;
    left: 40px;
    top: 150px;
    padding-left: 16px;
    border-left: 8px solid var(--accent);
  }
  .person__name { font-family: "Tinos", serif; font-size: 28px; color: var(--ink); line-height: 1; }
  .person__title { font-family: "Tinos", serif; font-size: 17px; color: var(--accent); margin-top: 4px; }

  .contacts {
    position: absolute;
    left: 72px;
    top: 222px;
    list-style: none;
    font-family: "Open Sans", sans-serif;
    font-size: 15px;
    color: var(--ink-soft);
  }
  .contacts li { display: flex; align-items: center; gap: 12px; height: 22px; }
  .contacts svg { width: 16px; height: 14px; flex: none; }
</style>
</head>
<body>
  <section class="card card--front" aria-label="Card front">
    <div class="brand">
      <div class="brand__mark"></div>
      <div class="brand__name">Blue Heron Partners</div>
    </div>
    <div class="person">
      <div class="person__name">Your Name</div>
      <div class="person__title">Job Title</div>
    </div>
    <ul class="contacts">
      <li>
        <svg viewBox="0 0 16 14" aria-hidden="true"><path fill="#d40f0f" d="M1 4c0-2 3-3 7-3s7 1 7 3v1h-3V4H4v1H1z M3 6h10l1 7H2z"/><circle cx="8" cy="9.5" r="2" fill="#e4e1da"/></svg>
        000 000 0000
      </li>
      <li>
        <svg viewBox="0 0 16 14" aria-hidden="true"><rect x="1" y="2" width="14" height="10" fill="#d40f0f"/><path d="M1 2l7 6 7-6" fill="none" stroke="#e4e1da" stroke-width="1.3"/></svg>
        youremail@xyz.com
      </li>
      <li>
        <svg viewBox="0 0 16 14" aria-hidden="true"><g fill="none" stroke="#d40f0f" stroke-width="1.2"><circle cx="8" cy="7" r="6"/><ellipse cx="8" cy="7" rx="2.6" ry="6"/><path d="M2 7h12M3 4h10M3 10h10"/></g></svg>
        blueheronpartners.com
      </li>
    </ul>
  </section>

  <section class="card card--back" aria-label="Card back">
    <div class="brand">
      <div class="brand__mark"></div>
      <div class="brand__name">Blue Heron Partners</div>
    </div>
  </section>
</body>
</html>
```